Supplement Brand Product Labels

Product Label for Supplement Brand

Protein Powder Label (2 x different flavours)

Neon Colours / Skull / Spooky
Refer to pictures below, they are the look we are wanting to go with but put our touch to it aswell.

Target Market(s)

Fitness

Industry/Entity Type

Supplement Brand

Colors
0054AA
0677BA
7BADD7
CADEEF
E8F1F8
0094D4
00A9DD
6FCCEA
C7EBF8
E9F6FB
00AB8E
00BBA5
67D7C9
C6EFE9
E9F9F6
59FF00
82FF00
B8FF75
E3FFCB
F4FFEA
FFF300
FFF600
FEFA6F
FFFEC7
FFFEE8
FFC000
F8CF3A
FAE287
FDF2CF
FEFAEE
F0912C
F2A743
F7CA91
FBE8D2
FDF5EE
EE7325
F08F49
F5BC92
FAE3D3
FDF4ED
EB3D1F
EC4F4E
F09395
F8D3D4
FCEDEE
E54698
E96AAD
F1A4CE
F9D9EA
FCEFF6
A7469A
B969AE
D3A5CF
EDDBEB
F8F0F9
6B429C
8869AF
B7A5CE
E3DAEB
F3F0F8

Requirements
Nice to have
• Skull, Neon Colours, Abstract, Barbell, Lighting Bolt, Flames, Spooky

```html
<!DOCTYPE html>
<html lang="en">
<head>
<meta charset="utf-8">
<title>Voltcore Supps BCAA Label</title>
<link rel="stylesheet" href="https://fonts.googleapis.com/css2?family=Anton&family=Fira+Sans+Condensed:wght@400;600;700&family=Permanent+Marker&display=swap">
<style>
  :root {
    --ink: #000000;
    --paper: #ffffff;
    --neon-blue: #0094d4;
    --ice-blue: #00a9dd;
    --glow: #6fccea;
    --deep: #0054aa;
  }
  * { margin: 0; padding: 0; box-sizing: border-box; }
  html, body { width: 1200px; height: 484px; overflow: hidden; background: var(--ink); }
  .label {
    position: relative; width: 1200px; height: 484px; overflow: hidden;
    background: var(--ink); color: var(--paper);
    font-family: "Fira Sans Condensed", sans-serif;
  }
  .skull-art {
    position: absolute; left: 250px; top: 0; width: 520px; height: 484px;
    background:
      radial-gradient(ellipse 38% 45% at 50% 50%, rgba(111,204,234,0.55), rgba(0,148,212,0.35) 45%, rgba(0,84,170,0.15) 70%, transparent 100%),
      radial-gradient(ellipse 50% 60% at 50% 45%, rgba(0,169,221,0.25), transparent 80%);
  }
  .directions { position: absolute; left: 54px; top: 25px; width: 200px; }
  .section-title { color: var(--neon-blue); font-weight: 700; font-size: 18px; margin-bottom: 8px; }
  .directions p { font-weight: 600; font-size: 12px; line-height: 14.4px; margin-bottom: 14px; }
  .side-brand { position: absolute; left: 58px; top: 322px; font-family: "Anton", sans-serif; font-size: 40px; line-height: 1; color: var(--paper); letter-spacing: 1px; }
  .side-brand-sub { position: absolute; left: 60px; top: 368px; font-family: "Anton", sans-serif; font-size: 18px; color: var(--paper); }
  .contact { position: absolute; left: 58px; top: 396px; font-weight: 600; }
  .contact .web { font-size: 14px; margin-bottom: 5px; margin-left: 10px; }
  .contact .addr { font-size: 11px; }
  .hero-brand { position: absolute; left: 470px; top: 40px; width: 340px; text-align: center; font-family: "Anton", sans-serif; color: var(--paper); line-height: 0.95; }
  .hero-brand .name { font-size: 92px; letter-spacing: 2px; }
  .hero-brand .sub { font-size: 38px; letter-spacing: 6px; }
  .product { position: absolute; left: 560px; top: 228px; width: 210px; text-align: center; font-family: "Permanent Marker", cursive; }
  .product .type { font-size: 64px; color: var(--paper); line-height: 1; }
  .product .ratio { font-size: 54px; color: var(--neon-blue); line-height: 1.1; margin-top: 6px; }
  .flavour { position: absolute; left: 566px; top: 396px; width: 200px; text-align: center; font-weight: 700; font-size: 17px; letter-spacing: -0.3px; }
  .weight { position: absolute; left: 566px; top: 428px; width: 200px; text-align: center; font-weight: 700; font-size: 24px; }
  .nutrition { position: absolute; left: 868px; top: 27px; width: 312px; height: 274px; background: var(--paper); border: 3px solid #222; color: var(--ink); }
  .nutrition table { width: 100%; border-collapse: collapse; }
  .nutrition th { font-weight: 700; font-size: 10px; line-height: 12px; text-align: center; padding: 5px 4px; height: 51px; border-bottom: 3px solid #222; vertical-align: bottom; }
  .nutrition th:first-child { text-align: left; padding-left: 6px; }
  .nutrition td { font-size: 11.5px; height: 31px; text-align: center; }
  .nutrition td:first-child { text-align: left; padding-left: 6px; width: 44%; }
  .ingredients { position: absolute; left: 877px; top: 322px; }
  .ingredients h2 { color: var(--neon-blue); font-size: 19px; font-weight: 700; letter-spacing: 0.5px; margin-bottom: 5px; }
  .ingredients p { color: var(--neon-blue); font-size: 12px; font-weight: 600; letter-spacing: -0.3px; }
  .origin { position: absolute; left: 916px; top: 420px; display: flex; align-items: center; gap: 6px; }
  .origin-map { width: 36px; height: 32px; background: var(--neon-blue); border-radius: 40% 50% 45% 30%; }
  .origin-text { font-family: "Anton", sans-serif; font-size: 16px; line-height: 16px; letter-spacing: 1px; }
</style>
</head>
<body>
<main class="label">
  <div class="skull-art" role="img" aria-label="Glowing blue skull surrounded by neon blue flames"></div>

  <section class="directions">
    <h2 class="section-title">Directions Of Use</h2>
    <p>Mix 5g (1 scoop) with 250ml's of cold water and consume immediately.</p>
    <p>Formulated supplementary sports food. Not suitable for children under 15 years of age or pregnant women. Should only be used under medical or dietetic supervision. This product is not a sole source of nutrition and should be consumed in conjunction with a nutritious diet and appropriate physical training or exercise program.</p>
    <p>Store in a cool dry place out of direct sunlight.</p>
  </section>

  <div class="side-brand">VOLTCORE</div>
  <div class="side-brand-sub">SUPPS</div>
  <div class="contact">
    <div class="web">www.voltcoresupps.com</div>
    <div class="addr">PO BOX 118, Redcliffe QLD 4020</div>
  </div>

  <div class="hero-brand">
    <div class="name">VOLTCORE</div>
    <div class="sub">SUPPS</div>
  </div>

  <div class="product">
    <div class="type">BCAA</div>
    <div class="ratio">2:1:1</div>
  </div>
  <div class="flavour">Raspberry Lemonade</div>
  <div class="weight">250G</div>

  <section class="nutrition">
    <table>
      <thead>
        <tr>
          <th>35.7 Servings<br>Per 250g Packet<br>7 Grams Per Serve</th>
          <th>Average Quantity<br>Per Serving</th>
          <th>Average Quantity<br>Per 100g</th>
        </tr>
      </thead>
      <tbody>
        <tr><td>Energy (KJ)</td><td>119</td><td>1700</td></tr>
        <tr><td>Protein (G)</td><td>7</td><td>100</td></tr>
        <tr><td>Total Carbohydrates (G)</td><td>0</td><td>0</td></tr>
        <tr><td>(Sugar) (G)</td><td>0</td><td>0</td></tr>
        <tr><td>Total Fats (G)</td><td>0</td><td>0</td></tr>
        <tr><td>Sodium (MG)</td><td>0</td><td>0</td></tr>
        <tr><td>BCAA 2:1:1 (G)</td><td>7</td><td>100</td></tr>
      </tbody>
    </table>
  </section>

  <section class="ingredients">
    <h2>Ingredients</h2>
    <p>Arginine Alpha-Ketoglutarate</p>
  </section>

  <div class="origin">
    <div class="origin-map" role="img" aria-label="Map outline of Australia"></div>
    <div class="origin-text">MADE IN<br>AUSTRALIA</div>
  </div>
</main>
</body>
</html>
```